Celvara Health Group Presentation Folder, for Cancer Awareness, VERY COLORFUL AND MODERN

Presentation Folder I know pretty much what i want so it should be very eazy , I have included files from folders I use now rebrand them to my new company they will be fine, no sense re creating the wheel
Full Bleed Size
20.87" x 16.68"
53 x 42.4 cm
6260 x 5004 pixels
Document Trim Size
20.75" x 16.56"
52.7 x 42.1 cm
6225 x 4969 pixels

Low design quality

Industry/Entity Type

Medical

Font styles to use
Serif

Colors

Designer to choose colors to be used in the design.

Requirements
Must have
• really I am not looking for some one to redesign, we like our folder front page and would like to see new word information added., there are two folder front pages to choose from
• So Keep the original front page and redesign the back page and the pockets
• Can Make your Design off of one of the ones I already uploaded
Nice to have
• Keep the same color schemes, Keep the original front page and redesign the back page and the pockets
Should not have
• DO not recreate the front covers, use what I gave you and just rebrand

```html
<!DOCTYPE html>
<html lang="en">
<head>
<meta charset="utf-8">
<title>Celvara Health Group – Hereditary Cancer Screening Folder</title>
<link href="https://fonts.googleapis.com/css2?family=Raleway:wght@300;400;500;600;700;800&display=swap" rel="stylesheet">
<style>
  :root{
    --backdrop:#5c5c5c;
    --paper:#ffffff;
    --navy:#0c1a55;
    --pink:#ee7f9c;
    --green:#7cc230;
    --grey-band:#77777a;
    --frame:#7fd0ef;
    --cut:#e0373c;
    --fold:#3cc47a;
    --ink:#222222;
    --muted:#555555;
    --photo-blue:#6aa6e2;
    --photo-warm:#c9b8a6;
    --ribbon:#b98fe0;
  }
  *{margin:0;padding:0;box-sizing:border-box}
  html,body{width:1200px;height:1000px;overflow:hidden;background:var(--backdrop)}
  .folder{position:relative;width:1200px;height:1000px;font-family:'Raleway',sans-serif;color:var(--ink)}
  .dieline{position:absolute;inset:0}
  .abs{position:absolute}

  .panel-frame{position:absolute;border:1px solid var(--frame)}
  .panel-frame.back{left:106px;top:76px;width:476px;height:606px}
  .panel-frame.front{left:618px;top:76px;width:476px;height:606px}

  .photo{position:absolute;box-shadow:0 6px 10px rgba(0,0,0,.25)}
  .photo.beach{left:128px;top:178px;width:420px;height:284px;transform:rotate(-5deg);background:var(--photo-blue)}
  .photo.table{left:660px;top:290px;width:420px;height:262px;transform:rotate(-5deg);background:var(--photo-warm)}
  .ribbon{position:absolute;width:40px;height:74px;background:var(--ribbon)}
  .ribbon.r1{left:486px;top:120px}
  .ribbon.r2{left:1014px;top:216px}

  .back-copy{left:126px;top:516px;width:424px;font-size:10.2px;line-height:12.4px;color:var(--ink)}
  .back-copy .lead{color:var(--green);font-weight:700}
  .back-copy .slogan{margin-top:18px;color:var(--navy);font-size:11.4px;line-height:13.6px;font-weight:500}
  .back-copy .note{margin-top:16px;color:var(--navy);font-size:11.4px;line-height:13.6px;font-weight:500}

  .front-title{left:618px;top:116px;width:490px;text-align:center;color:var(--pink);font-weight:600;font-size:24.5px;letter-spacing:2.2px}
  .front-sub{left:618px;top:152px;width:476px;text-align:center;font-size:14px;font-weight:500;color:#111}
  .front-body{left:660px;top:181px;width:400px;text-align:center;font-size:11.5px;line-height:13.5px;font-weight:400;color:var(--muted)}

  .tag-band{left:600px;top:598px;width:554px;height:36px;background:var(--grey-band)}
  .tag-band p{position:absolute;left:142px;top:8px;color:#fff;font-size:16.5px;font-weight:300}
  .brand-dot{left:676px;top:608px;width:46px;height:46px;border-radius:50%;background:#fff;border:3px solid var(--navy)}
  .brand-name{left:640px;top:658px;width:120px;text-align:center;font-size:9px;font-weight:700;color:var(--navy)}

  .pocket-left-content{left:124px;top:718px;width:436px;height:206px;transform:rotate(180deg)}
  .pocket-left-content .company{position:absolute;left:0;right:0;top:164px;text-align:center;font-weight:800;font-size:14px;color:var(--navy)}
  .pocket-left-content .division{position:absolute;left:0;right:0;top:184px;text-align:center;font-size:11px;color:#222}
  .pocket-left-content .mark-dot{position:absolute;left:166px;top:88px;width:26px;height:26px;border-radius:50%;background:var(--navy)}
  .pocket-left-content .mark-name{position:absolute;left:200px;top:93px;font-size:13px;font-weight:700;color:var(--navy)}

  .pocket-right-content{left:630px;top:718px;width:436px;height:206px;transform:rotate(180deg);color:#fff}
  .pocket-right-content .inner{position:absolute;left:26px;top:30px;width:352px}
  .pocket-right-content .fine{font-size:6.4px;line-height:8px;margin-bottom:6px}
  .pocket-right-content h2{font-weight:800;font-size:15px;line-height:20px;margin-top:8px}
  .pocket-right-content h2 .accent{color:var(--green)}
</style>
</head>
<body>
<div class="folder">
  <svg class="dieline" width="1200" height="1000" viewBox="0 0 1200 1000" aria-hidden="true">
    <path d="M48,60 H1156 V444 A18,18 0 0 0 1156,480 V700 H48 V480 A18,18 0 0 0 48,444 Z" fill="#fff" stroke="var(--cut)" stroke-width="1"/>
    <path d="M92,700 H596 L568,910 Q562,944 530,944 H92 Z" fill="#fff" stroke="var(--cut)" stroke-width="1"/>
    <path d="M604,700 H1112 V944 H676 Q642,944 636,910 Z" fill="var(--navy)" stroke="var(--cut)" stroke-width="1"/>
    <line x1="600" y1="60" x2="600" y2="700" stroke="var(--fold)" stroke-dasharray="3 3"/>
    <line x1="92" y1="700" x2="1112" y2="700" stroke="var(--fold)" stroke-dasharray="3 3"/>
    <path d="M124,718 H560 L536,900 Q530,924 504,924 H124 Z" fill="none" stroke="var(--frame)"/>
    <path d="M630,718 H1066 V924 H690 Q664,924 658,900 Z" fill="none" stroke="var(--frame)"/>
    <g stroke="var(--cut)" stroke-width="1">
      <line x1="280" y1="772" x2="246" y2="804"/>
      <line x1="406" y1="772" x2="440" y2="804"/>
      <line x1="246" y1="852" x2="280" y2="886"/>
      <line x1="440" y1="852" x2="406" y2="886"/>
    </g>
  </svg>

  <div class="panel-frame back"></div>
  <div class="panel-frame front"></div>

  <div class="photo beach" role="img" aria-label="Photo of a three-generation family in white walking hand in hand on a sunny beach"></div>
  <div class="ribbon r1" role="img" aria-label="Pink and blue cancer awareness ribbon"></div>

  <div class="abs back-copy">
    <p><span class="lead">Hereditary cancer screening</span> provides vital information to help people with a strong personal or family history of cancer understand their own risk of developing the disease. With this information, they can take steps to Potentially Prevent Cancer, Delay the Onset of Cancer or Catch it at an Earlier stage when outcomes and survival rates are Better.</p>
    <p class="slogan">Don't be Afraid of the Answer: Knowledge is Power and Power Eradicates Fear. When You are Fearless, You Will Make all the Right Choices!</p>
    <p class="note">Directions – USE any family picture I provided AND THE WORDS -Use you creativity to make it nice</p>
  </div>

  <h1 class="abs front-title">HEREDITARY CANCER SCREENING</h1>
  <p class="abs front-sub">Doctors are the Gatekeepers to Genetic Testing.</p>
  <p class="abs front-body">We have an obligation to help patients understand genetic risk and how testing can guide heath care decisions.</p>
  <div class="photo table" role="img" aria-label="Photo of a family of three generations sharing a meal at an outdoor table"></div>
  <div class="ribbon r2" role="img" aria-label="Pink and blue cancer awareness ribbon"></div>

  <div class="abs tag-band"><p>The test you order FOR your patients</p></div>
  <div class="abs brand-dot" aria-hidden="true"></div>
  <p class="abs brand-name">Celvara Health Group</p>

  <div class="abs pocket-left-content">
    <div class="mark-dot" aria-hidden="true"></div>
    <p class="mark-name">Celvara Health Group</p>
    <p class="company">Celvara Health Group</p>
    <p class="division">a division of Northfield Medical Sales LLC</p>
  </div>

  <div class="abs pocket-right-content">
    <div class="inner">
      <p class="fine">There are many benefits to getting tested, regardless of the eventual result. If one of your family members – however distant – had cancer, there is a chance that you inherited a gene mutation that not only increases your personal risk of cancer, but also could be passed to the next generation. Those who are carriers of hereditary cancer gene mutations, could be at risk of getting cancer earlier in life than the general population. The sooner genetic testing is done, the more likely it is that the risk can be managed appropriately.</p>
      <p class="fine">Hereditary cancer screening provides vital information to help people with a strong personal or family history of cancer understand their own risk of developing the disease. With this information, they can take steps to Potentially Prevent Cancer, Delay the Onset of Cancer or Catch it at an Earlier stage when outcomes and survival rates are Better.</p>
      <h2>Identifying an inherited genetic<br>mutation has the potential to prevent cancer<br><span class="accent">and save lives.</span></h2>
    </div>
  </div>
</div>
</body>
</html>
```